KRBL informational brochure to aimed to attract people to all three our our service industries

This brochure is designed to be multi purposed, here are a few objectives:
1. To provide a receipt for septic services rendered onsite to customers. The receipt has coupons to entice each customer to use us in the future. This brochure also gives this customer tips on how to best keep their septic system from developing issues. By providing additional company information the septic customer can become educated about the other lines of service we provide in the area, i.e. Trash pick up, & roll-off dumpsters. Optimally we would want a septic customer to be so impressed with our septic work that they would trust us to serve them in the other areas we offer.
2. The brochure is a means of obtaining ratings and reviews for our online profiles, i.e. Zapmo, & Berta's roll. It is already hard enough to get a customer to give us 5-star ratings, so this is a useful tool to try and bait the customer to get a price reduction on their total cost for septic services by rating us or performing an online review. We want to have a place on the brochure that references our current 5-star ratings on Zapmo, Chatterpage, and Berta's roll see the attached example.
3. This brochure is not only useful for septic clients but can also be used for general advertising, we leave these brochures in a variety of public locations. Thus it would be efficient to show all lines of business and provide the information needed to acquire new clients.
4. Photographs are a critical component of our plan, customers like to SEE what we do and who we are. Thus, please find a creative way of including photos of what we offer by means of services and products. For individuals who have seen our brand around town, a photographic reminder might help this potential clients to recognizing who we are.
5. I will attach a copy of our last MakerBazaar project to this project to give you an idea of how we like to present ourselves.
6. We want to encourage the Spanish speaking individuals to call us for translated material.
7. We need to mention pricing on this brochure for all 3 lines of business, i'll find a way to provide those to you.
8. We don't know what size to choose, one size is 8.5'' x 11'' the other size is 8.5'' x 14'. Perhaps you can help us choose. not sure if we should have a trifold (3 pane) or quadfold (4 pane) brochure. We want to express ourselves creatively and not just provide boring information.
9. we need to have an american flag somewhere on display
Target Market(s)
Rural areas of North Texas, Our office is in Ponder TX and we serve 35 mile radius.
Industry/Entity Type
Waste Management

```html
<!DOCTYPE html>
<html lang="en">
<head>
<meta charset="utf-8">
<title>KRBL Services Brochure – Inside Spread</title>
<link href="https://fonts.googleapis.com/css2?family=Lato:ital,wght@0,400;0,700;0,900;1,700&family=Bitter:ital,wght@1,700&display=swap" rel="stylesheet">
<style>
  :root {
    --ink: #0b0b0b;
    --gold: #f6c81b;
    --white: #ffffff;
    --muted: #e9e9e9;
  }
  * { box-sizing: border-box; margin: 0; padding: 0; }
  html, body { width: 1200px; height: 800px; overflow: hidden; background: var(--ink); }
  .brochure { position: relative; width: 1200px; height: 800px; font-family: "Lato", sans-serif; color: var(--white); }
  .backdrop { position: absolute; inset: 0; }
  .panel-title { position: absolute; font-weight: 900; font-size: 15px; letter-spacing: .3px; text-transform: uppercase; color: var(--gold); }
  .panel-title.septic { color: var(--ink); text-align: center; font-size: 13px; line-height: 1.2; }
  .photo-caption { position: absolute; left: 34px; top: 122px; font-weight: 700; font-size: 15px; color: var(--ink); }
  .copy { position: absolute; font-size: 13.5px; line-height: 1.38; }
  .copy h2 { color: var(--gold); font-size: 18px; font-weight: 900; padding-bottom: 4px; border-bottom: 1.5px solid var(--white); margin-bottom: 6px; }
  .copy h3 { color: var(--gold); font-size: 16px; font-weight: 900; margin: 10px 0 4px; }
  .copy p { margin-bottom: 6px; }
  .copy .accent { color: var(--gold); font-weight: 700; }
  .ticks { list-style: none; margin: 4px 0 8px; }
  .ticks li { position: relative; padding-left: 22px; margin-bottom: 3px; }
  .ticks li::before {
    content: ""; position: absolute; left: 0; top: 3px; width: 13px; height: 13px;
    border: 2px solid var(--gold); border-radius: 50%;
  }
  .ticks li::after {
    content: ""; position: absolute; left: 4px; top: 6px; width: 6px; height: 3px;
    border-left: 2px solid var(--gold); border-bottom: 2px solid var(--gold); transform: rotate(-45deg);
  }
  .panel-left { left: 34px; top: 372px; width: 340px; }
  .panel-mid { left: 430px; top: 362px; width: 340px; }
  .panel-mid h2 { text-align: center; }
  .panel-right { left: 830px; top: 338px; width: 340px; }
  .callout { position: absolute; right: 30px; top: 244px; text-align: right; }
  .callout .tagline { color: var(--gold); font-weight: 900; font-size: 22px; line-height: 1.05; }
  .callout .phone { color: var(--white); font-weight: 900; font-size: 22px; margin-top: 2px; }
  .promise { position: absolute; font-family: "Bitter", serif; font-style: italic; font-weight: 700; color: var(--ink); font-size: 17px; white-space: nowrap; }
  .promise::before { content: "✓ "; font-style: normal; }
</style>
</head>
<body>
<main class="brochure">
  <svg class="backdrop" width="1200" height="800" viewBox="0 0 1200 800" aria-hidden="false">
    <defs>
      <clipPath id="photo-band">
        <path d="M0,105 C150,100 300,95 400,92 C520,88 700,85 790,70 C830,62 840,20 880,0 L1200,0 L1200,180 C1170,210 1100,220 1000,245 C900,270 850,300 780,320 C700,340 550,330 400,335 C350,345 200,345 0,355 Z"/>
      </clipPath>
      <linearGradient id="sky-yellow" x1="0" y1="0" x2="0" y2="1">
        <stop offset="0" stop-color="#8fb7e0"/><stop offset=".45" stop-color="#d8c23a"/><stop offset="1" stop-color="#7f8f4a"/>
      </linearGradient>
      <linearGradient id="sun-dumpster" x1="0" y1="0" x2="1" y2="1">
        <stop offset="0" stop-color="#dfe6e8"/><stop offset=".5" stop-color="#3a3a34"/><stop offset="1" stop-color="#6d6a5e"/>
      </linearGradient>
      <linearGradient id="field-truck" x1="0" y1="0" x2="0" y2="1">
        <stop offset="0" stop-color="#9cc2e6"/><stop offset=".5" stop-color="#5d6f3a"/><stop offset="1" stop-color="#8a7a4e"/>
      </linearGradient>
    </defs>
    <rect width="1200" height="800" fill="var(--ink)"/>
    <g clip-path="url(#photo-band)">
      <rect role="img" aria-label="Photo of a yellow front-load dumpster and black trash toter on a sunny lawn" x="0" y="0" width="400" height="400" fill="url(#sky-yellow)"/>
      <rect role="img" aria-label="Photo of a black roll-off dumpster on gravel in morning sunlight" x="400" y="0" width="400" height="400" fill="url(#sun-dumpster)"/>
      <rect role="img" aria-label="Photo of a septic pump truck with a green hose across a rural field" x="800" y="0" width="400" height="400" fill="url(#field-truck)"/>
    </g>
    <path d="M0,105 C150,100 300,95 400,92 C520,88 700,85 790,70 C830,62 840,20 880,0" fill="none" stroke="var(--gold)" stroke-width="8"/>
    <path d="M0,355 C200,345 350,345 400,335 C550,330 700,340 780,320 C850,300 900,270 1000,245 C1100,220 1170,210 1200,180" fill="none" stroke="var(--gold)" stroke-width="8"/>
    <path d="M0,752 C300,740 600,748 800,722 C950,702 1100,692 1200,672 L1200,800 L0,800 Z" fill="var(--gold)"/>
  </svg>

  <h1 class="panel-title" style="left:40px; top:50px;">Residential Waste Collections</h1>
  <h1 class="panel-title" style="left:520px; top:42px;">Roll-Off Dumpsters</h1>
  <h1 class="panel-title septic" style="left:1030px; top:24px;">Septic Pumping<br>&amp; Cleaning</h1>

  <p class="photo-caption">Military, Senior, Clergy &amp; Seasonal Discounts</p>

  <section class="copy panel-left">
    <h2>We don't talk trash, we talk solutions!</h2>
    <p>Our local team provides professional, friendly, small-town customer service that you won't find anywhere else.</p>
    <p>There are multiple packages to meet any budget:</p>
    <p class="accent">Toters - Starting at $19.99/ per month!</p>
    <ul class="ticks">
      <li>2 yard Dumpsters<br>Start up special $55 per month!</li>
      <li>Bagged Trash Service</li>
      <li>Bulk pick-up &amp; Garage clean outs</li>
      <li>See all the Discounts above!</li>
    </ul>
    <p>We strive to offer dependable and affordable residential trash removal throughout Denton County &amp; all the surrounding areas.</p>
  </section>

  <section class="copy panel-mid">
    <h2>No project is too big!</h2>
    <p>KRBL offer a variety of roll-off and construction dumpsters that are ready to meet the needs of any construction or demolition project. From a small renovation or landscape project, to new building constructions</p>
    <ul class="ticks">
      <li>24-hour turn around time</li>
      <li>Competitive pricing</li>
      <li>Complementary Tonnage</li>
      <li>Friendly teammate always available to take your order</li>
    </ul>
    <p>We provide reliable waste hauling services:</p>
    <p class="accent">Starting at $450/ haul</p>
  </section>

  <div class="callout">
    <p class="tagline">Let us do<br>the dirty work!</p>
    <p class="phone">(555)014-2270</p>
  </div>

  <section class="copy panel-right">
    <h2>Septic Pumping &amp; Cleaning</h2>
    <p>Pump &amp; clean services <span class="accent">starting at $350 for conventional and $450 for aerobic systems!</span></p>
    <p>We take pride in our work and are dedicated to offering the highest-quality septic pumping services available.</p>
    <p>From cesspools and septic tanks to sewage pits and beyond, you can depend on our experienced technicians to get the job done right. Sit back and relax while we take care of the dirty work.</p>
    <h3>Other Services</h3>
    <ul class="ticks">
      <li>Electronic tank location services</li>
      <li>Camera Snaking</li>
      <li>Emergency Septic Repairs</li>
      <li>Real Estate Septic Inspections</li>
    </ul>
  </section>

  <p class="promise" style="left:30px; top:762px;">No Administration Fees</p>
  <p class="promise" style="left:260px; top:758px; font-size:15px;">No Contracts</p>
  <p class="promise" style="left:430px; top:752px;">No Hidden Fees</p>
  <p class="promise" style="left:600px; top:742px; font-size:15px;">No Fuel Surcharges</p>
  <p class="promise" style="left:800px; top:728px;">Online Billing or Billing Made Simple.</p>
</main>
</body>
</html>
```